A Label for an ECO Friendly Spirit Company

Design a label which can be used for vodka and gin (London Dry Gin). It should be Square type Like the Shape File you see in the uploads. KIRO means Kind Inventive Rare and Original. We want a cool and slim label that calls for eco-friendly. We want to use it for our premium
Vodka and our London Dry Gin. Please use the logo and design it in Square Type.

40%vol, 700ml

Target Market(s)

spirits and events

Industry/Entity Type

SPIRITS

Colors
00AB8E
00BBA5
67D7C9
C6EFE9
E9F9F6
59FF00
82FF00
B8FF75
E3FFCB
F4FFEA

Requirements
Must have
• Logo from KIRO, Squaee Shape

```html
<!DOCTYPE html>
<html lang="en">
<head>
<meta charset="utf-8">
<title>KIRO Spirit Label</title>
<link rel="stylesheet" href="https://fonts.googleapis.com/css2?family=Montserrat:wght@400;600&display=swap">
<style>
  :root {
    --page: #ffffff;
    --frame-green: #8dc63f;
    --label-cream: #e3ffcb;
    --label-pale: #f4ffea;
    --teal: #00ab8e;
    --teal-line: #00bba5;
    --stripe-mint: #b8f0cc;
    --stripe-deep: #a4e6c4;
  }
  html, body {
    margin: 0;
    padding: 0;
    width: 1200px;
    height: 1200px;
    overflow: hidden;
    background: var(--page);
  }
  .label-canvas {
    display: block;
    width: 1200px;
    height: 1200px;
  }
  .frame-outer { fill: var(--frame-green); }
  .frame-inner { fill: var(--label-cream); }
  .frame-rule { fill: none; stroke: var(--teal-line); stroke-width: 2; }
  .frame-dashed { fill: none; stroke: var(--teal-line); stroke-width: 2; stroke-dasharray: 12 8; }
  .stripe-side { fill: var(--stripe-mint); }
  .stripe-centre { fill: var(--stripe-deep); }
  .brand-square { fill: var(--frame-green); }
  .brand-name {
    font-family: 'Montserrat', sans-serif;
    font-weight: 600;
    font-size: 114px;
    fill: var(--teal);
    letter-spacing: 2px;
  }
  .tagline-band-green { fill: var(--frame-green); }
  .tagline-band-teal { fill: var(--teal); }
  .tagline-text {
    font-family: 'Montserrat', sans-serif;
    font-weight: 400;
    font-size: 31px;
    fill: var(--label-cream);
    letter-spacing: 2px;
  }
  .spec-text {
    font-family: 'Montserrat', sans-serif;
    font-weight: 400;
    font-size: 24px;
    fill: var(--teal);
  }
</style>
</head>
<body>
<svg class="label-canvas" viewBox="0 0 1200 1200" xmlns="http://www.w3.org/2000/svg">
  <g transform="translate(600 600)">
    <!-- diamond frame -->
    <polygon class="frame-outer" points="0,-560 560,0 0,560 -560,0"/>
    <polygon class="frame-inner" points="0,-514 514,0 0,514 -514,0"/>
    <polygon class="frame-rule" points="0,-498 498,0 0,498 -498,0"/>
    <polygon class="frame-dashed" points="0,-478 478,0 0,478 -478,0"/>

    <!-- top stripes -->
    <polygon class="stripe-side" points="-39,-415 -23,-431 -23,-268 -39,-268"/>
    <polygon class="stripe-centre" points="-8,-451 0,-459 8,-451 8,-268 -8,-268"/>
    <polygon class="stripe-side" points="25,-431 41,-415 41,-268 25,-268"/>

    <!-- bottom stripes -->
    <polygon class="stripe-side" points="-39,268 -23,268 -23,462 -39,446"/>
    <polygon class="stripe-centre" points="-8,268 8,268 8,478 0,486 -8,478"/>
    <polygon class="stripe-side" points="25,268 41,268 41,446 25,462"/>

    <!-- brand mark -->
    <rect class="brand-square" x="-82" y="-222" width="168" height="174" rx="16"/>
    <text class="brand-name" x="0" y="48" text-anchor="middle">KIRO</text>

    <!-- taglines -->
    <rect class="tagline-band-green" x="-231" y="85" width="462" height="59"/>
    <text class="tagline-text" x="0" y="126" text-anchor="middle">KIND INVENTIVE</text>
    <rect class="tagline-band-teal" x="-197" y="164" width="394" height="58"/>
    <text class="tagline-text" x="0" y="204" text-anchor="middle">RARE AND ORIGINAL</text>

    <!-- specs -->
    <text class="spec-text" x="-100" y="285" text-anchor="middle">700ml</text>
    <text class="spec-text" x="105" y="285" text-anchor="middle">40%vol</text>
  </g>
</svg>
</body>
</html>
```